Half page (a5) ad for a company

I need a design for an ad for a company to be published in a conference catalogue. Please find enclosed the logo for a company. The company is providing health screening services. Ad should be subtle and minimalistic, i.e. logo in the centre and a phrase saying: "Be in charge of your own health" and the website bluefen.co.uk. Also please find enclosed guidlines for colours and fonts to be used.

```html
<!DOCTYPE html>
<html lang="en">
<head>
<meta charset="utf-8">
<title>Bluefen Private – Ad</title>
<link rel="stylesheet" href="https://fonts.googleapis.com/css2?family=Montserrat:wght@400;700&display=swap">
<style>
  :root {
    --brand-red: #ec1c24;
    --paper: #ffffff;
    --ink: #111111;
    --backdrop: #ececec;
  }
  * { margin: 0; padding: 0; box-sizing: border-box; }
  html, body {
    width: 1200px;
    height: 1200px;
    overflow: hidden;
    background: var(--backdrop);
    font-family: "Montserrat", sans-serif;
  }
  .ad {
    position: absolute;
    left: 204px;
    top: 40px;
    width: 792px;
    height: 1120px;
    background: var(--paper);
    display: flex;
    flex-direction: column;
  }
  .brand-area {
    height: 750px;
    display: flex;
    flex-direction: column;
    align-items: center;
    justify-content: center;
    padding-top: 40px;
  }
  .brand-dot {
    width: 96px;
    height: 96px;
    border-radius: 50%;
    background: var(--brand-red);
    margin-bottom: 56px;
  }
  .brand-name {
    color: var(--brand-red);
    font-weight: 400;
    font-size: 76px;
    letter-spacing: 0.5px;
    line-height: 1;
  }
  .message-band {
    flex: 1;
    background: var(--brand-red);
    display: flex;
    flex-direction: column;
    align-items: center;
    padding-top: 100px;
  }
  .tagline {
    color: var(--paper);
    font-weight: 700;
    font-size: 40px;
    line-height: 1.2;
    text-align: center;
  }
  .website {
    margin-top: 26px;
    color: var(--ink);
    font-weight: 400;
    font-size: 23px;
    letter-spacing: 0.3px;
  }
</style>
</head>
<body>
  <main class="ad">
    <section class="brand-area">
      <div class="brand-dot"></div>
      <div class="brand-name">Bluefen Private</div>
    </section>
    <section class="message-band">
      <h1 class="tagline">Be in charge of your own health</h1>
      <p class="website">bluefen.co.uk</p>
    </section>
  </main>
</body>
</html>
```